Law Firm Website

We are a small California based law firm specializing in business, corporate and litigation matters. We need to have our website redesigned. We are looking for a new and fresh look for our site, keeping in mind that we are a law firm.
What we don't want:
**the traditional "gavel" and "scales of justice" look
**anything too crazy
What we do want:
**sophisticated yet modern and fresh corporate look and feel
**samples of websites we really like:
http://www.tarnwellhope.example
http://www.marrowgate.example/
we also like:
http://www.fenwoodastley.example/
http://www.qz.example/
http://www.brenhollow.example/
http://www.pvdn.example
http://www.nqrlaw.example/
The content will be whatever is currently on our website (www.okabelawgroup.example). We will be selecting the winner based on originality and keeping the above requirements in mind. Please note that the photos that you use will be the ones that we will be using, so choose wisely because the photos will make a difference.
Target Market(s)
Corporate clients
Industry/Entity Type
Law Firm
Look and feel

```html
<!DOCTYPE html>
<html lang="en">
<head>
<meta charset="utf-8">
<title>Okabe Law Group, LLP — Law Center</title>
<link rel="stylesheet" href="https://fonts.googleapis.com/css2?family=Oswald:wght@400;600;700&family=PT+Serif:wght@400;700&family=Open+Sans:wght@400;600;700&display=swap">
<style>
  :root{
    --ink:#111111;
    --paper:#ffffff;
    --brand:#1a8fd6;
    --rule:#cfcfcf;
    --muted:#8a8a8a;
    --photo-a:#d9d9d9;
    --photo-b:#9a9a9a;
    --footer:#0c0c0c;
    --footer-text:#9b9b9b;
  }
  *{margin:0;padding:0;box-sizing:border-box}
  html,body{width:900px;height:1200px;overflow:hidden;background:var(--paper)}
  body{position:relative;font-family:"Open Sans",Arial,sans-serif;color:var(--ink)}

  .phone-tab{position:absolute;right:0;top:0;width:190px;height:34px;background:var(--ink);border-bottom-left-radius:10px;display:flex;align-items:center;justify-content:center;gap:10px;color:var(--paper);font-size:13px;letter-spacing:.5px}

  .brand{position:absolute;left:42px;top:32px;width:260px}
  .brand-mark{width:44px;height:62px;background:var(--brand);display:block}
  .brand-name{margin-top:10px;font-family:"Oswald",sans-serif;font-weight:600;font-size:20px;color:var(--ink);letter-spacing:.2px}

  .main-nav{position:absolute;left:420px;right:0;top:76px;height:22px;border-bottom:1px solid var(--rule);display:flex;justify-content:flex-end}
  .main-nav a{font-family:"Open Sans",sans-serif;font-size:11px;font-weight:700;color:var(--ink);text-decoration:none;padding:0 26px;letter-spacing:.4px}

  .capitol{position:absolute;left:40px;top:190px;width:200px;height:230px;background:linear-gradient(180deg,#f2f2f2,#dcdcdc)}
  .team-photo{position:absolute;left:400px;top:160px;width:470px;height:430px;background:linear-gradient(180deg,var(--photo-a),var(--photo-b));border-radius:2px}

  .hero-title{position:absolute;left:40px;top:440px;font-family:"Oswald",sans-serif;font-weight:700;font-size:50px;letter-spacing:1px;line-height:1}
  .hero-copy{position:absolute;left:40px;top:508px;width:240px;font-family:"PT Serif",serif;font-size:13px;line-height:17px;color:#222}
  .hero-cta{position:absolute;left:40px;top:612px;font-family:"PT Serif",serif;font-size:13px;color:var(--ink);text-decoration:none;display:flex;align-items:center;gap:8px}

  .divider{position:absolute;left:40px;right:40px;top:705px;height:1px;background:var(--rule)}
  .divider-badge{position:absolute;left:424px;top:679px;width:52px;height:52px;border-radius:50%;background:var(--paper);border:1px solid var(--rule);display:flex;align-items:center;justify-content:center}

  .services{position:absolute;left:0;top:778px;width:900px;height:130px}
  .service{position:absolute;top:0;width:124px;height:124px;border-radius:50%;border:1px solid #e2e2e2;display:flex;align-items:center;justify-content:center;font-size:13px;color:#555;background:var(--paper)}
  .service.is-active{background:var(--ink);color:var(--paper);border-color:var(--ink)}

  .skyline{position:absolute;left:0;top:955px;width:900px;height:95px;background:linear-gradient(180deg,#ffffff 0%,#d2d2d2 55%,#a8a8a8 100%)}

  .site-footer{position:absolute;left:0;top:1050px;width:900px;height:150px;background:var(--footer);color:var(--footer-text)}
  .footer-col{position:absolute;top:14px}
  .footer-col h3{font-family:"Open Sans",sans-serif;font-weight:400;font-size:12px;letter-spacing:.5px;color:#bdbdbd;padding-bottom:6px;border-bottom:1px solid #2a2a2a;width:230px;margin-bottom:8px}
  .footer-col ul{list-style:none}
  .footer-col li{font-size:10px;line-height:16px;padding-left:12px;position:relative}
  .footer-col li::before{content:"";position:absolute;left:0;top:6px;width:4px;height:4px;border-right:1px solid var(--footer-text);border-top:1px solid var(--footer-text);transform:rotate(45deg)}
  .col-links{left:42px}
  .col-social{left:330px}
  .col-contact{left:620px;top:10px}
  .col-contact h3{font-family:"Oswald",sans-serif;font-size:26px;font-weight:400;border:none;color:#cfcfcf;letter-spacing:1px;width:auto;margin-bottom:6px;padding-bottom:0}
  .col-contact p{font-size:10px;line-height:15px;border-top:1px solid #2a2a2a;padding-top:6px;width:240px}
  .col-contact p + p{border:none;padding-top:0}
</style>
</head>
<body>

<div class="phone-tab">
  <svg width="14" height="14" viewBox="0 0 14 14" aria-hidden="true"><path d="M3 1h2l1 3-1.5 1a8 8 0 0 0 4.5 4.5L10 8l3 1v2c0 1-1 2-2 2C6 13 1 8 1 3c0-1 1-2 2-2z" fill="#ffffff"/></svg>
  <span>000-000-000</span>
</div>

<header class="brand">
  <span class="brand-mark"></span>
  <div class="brand-name">Okabe Law Group, LLP</div>
</header>

<nav class="main-nav">
  <a href="#">HOME</a><a href="#">ABOUT US</a><a href="#">SERVICES</a><a href="#">CONTACT US</a>
</nav>

<div class="capitol" role="img" aria-label="Line drawing of a capitol building"></div>
<div class="team-photo" role="img" aria-label="Photo of the firm's four attorneys in suits"></div>

<h1 class="hero-title">LAW CENTER</h1>
<p class="hero-copy">Lorem Ipsum is simply dummy text of the printing and typesetting industry. Lorem Ipsum has been the industry's standard dummy text ever since the 1500s, when a printer began.</p>
<a class="hero-cta" href="#">Get Advice now
  <svg width="10" height="10" viewBox="0 0 10 10" aria-hidden="true"><path d="M2 1l5 4-5 4" fill="none" stroke="#111" stroke-width="1.5"/></svg>
</a>

<div class="divider"></div>
<div class="divider-badge">
  <svg width="18" height="12" viewBox="0 0 18 12" aria-hidden="true" fill="none" stroke="#111" stroke-width="1.6">
    <path d="M2 2l7 7 7-7"/>
  </svg>
</div>

<section class="services">
  <div class="service is-active" style="left:84px">Services1</div>
  <div class="service" style="left:304px">Service2</div>
  <div class="service" style="left:494px">Service 3</div>
  <div class="service" style="left:704px">Service 4</div>
</section>

<div class="skyline" role="img" aria-label="Grey city skyline illustration"></div>

<footer class="site-footer">
  <div class="footer-col col-links">
    <h3>QUICK LINKS</h3>
    <ul><li>Home</li><li>Services</li><li>Contact Us</li><li>Privacy policy</li></ul>
  </div>
  <div class="footer-col col-social">
    <h3>SOCIAL</h3>
    <ul><li>Friendlane</li><li>Chirpline</li><li>Workweave</li><li>Blog</li></ul>
  </div>
  <div class="footer-col col-contact">
    <h3>LAW CENTER</h3>
    <p>410 Harbor Ave, Suite 200 Coastview, CA 90000</p>
    <p>P O Box 12, Phone: 000-000-000</p>
    <p>Copyright 2013 lawcenter.example</p>
  </div>
</footer>

</body>
</html>
```